Stylish Business Cards Wanted

- DOUBLE SIDED Design Required -

High end, edgy cards for a corporate and personal stylist. Must include logo,
Name: Belinda Harwick
Title: Director and Stylist
telephone : +61 8 7142 5809
email: belinda@theloombriefing.example
website: theloombriefing.example
Tag: Corporate Workwear & Uniform Specialist | Personal Stylist
Would like nice icons for telephone, email, website

Target Market(s)

Businesses wanting stylish uniforms, people wanting stylish wardrobes

Industry/Entity Type

Corporate Workwear Stylist

Contact Information for Business Card

I would like black, white and gold foiling incorporated in the design - possibly a touch of the other colours on my branding guide attached Name: Belinda Harwick Title: Director and Stylist telephone : +61 8 7142 5809 email: belinda@theloombriefing.example website: theloombriefing.example Tag: Corporate Workwear & Uniform Specialist | Personal Stylist Would like nice icons for telephone, email, website

Font styles to use
Other font styles liked:
• Raleway

Colors

Designer to choose colors to be used in the design.

Requirements
Must have
• Gold foil accents

```html
<!DOCTYPE html>
<html lang="en">
<head>
<meta charset="utf-8">
<title>The Loom Briefing – Business Cards</title>
<link rel="stylesheet" href="https://fonts.googleapis.com/css2?family=Raleway:wght@400;500;600;700&display=swap">
<style>
  :root {
    --gold: #e4bd58;
    --ink: #231f20;
    --card: #ffffff;
    --backdrop: #ececec;
    --rule: #3a3a3a;
  }
  * { margin: 0; padding: 0; box-sizing: border-box; }
  html, body { width: 1200px; height: 507px; overflow: hidden; }
  body {
    background: var(--backdrop);
    font-family: "Raleway", sans-serif;
    color: var(--ink);
    position: relative;
  }
  .card {
    position: absolute;
    top: 106px;
    width: 493px;
    height: 295px;
    background: var(--card);
    overflow: hidden;
    box-shadow: 0 6px 14px rgba(0,0,0,0.12);
  }
  .card--front { left: 83px; }
  .card--back { left: 624px; }

  .tab {
    position: absolute;
    top: 85px;
    width: 31px;
    height: 124px;
    background: var(--gold);
  }
  .tab--left { left: 0; border-radius: 0 12px 12px 0; }
  .tab--right { right: 0; border-radius: 12px 0 0 12px; }

  .brand-name {
    font-weight: 700;
    color: var(--ink);
    text-align: center;
    letter-spacing: 0.5px;
    line-height: 1.05;
  }
  .card--front .brand-name {
    position: absolute;
    left: 0; right: 0;
    top: 114px;
    font-size: 34px;
  }
  .tagline {
    position: absolute;
    left: 0; right: 0;
    top: 313px;
    top: 207px;
    text-align: center;
    font-size: 14.5px;
    font-weight: 400;
    white-space: nowrap;
  }
  .tagline .sep { color: var(--gold); margin: 0 6px; }

  .card--back .brand-name {
    position: absolute;
    left: 42px;
    width: 150px;
    top: 116px;
    font-size: 24px;
  }
  .divider {
    position: absolute;
    left: 197px;
    top: 93px;
    width: 1px;
    height: 109px;
    background: var(--rule);
  }
  .contact {
    position: absolute;
    left: 210px;
    top: 96px;
  }
  .person-name {
    color: var(--gold);
    font-weight: 600;
    font-size: 22px;
    line-height: 1;
    white-space: nowrap;
  }
  .person-title {
    font-size: 11px;
    margin-top: 5px;
  }
  .contact-list { list-style: none; margin-top: 7px; }
  .contact-list li {
    display: flex;
    align-items: center;
    font-size: 14px;
    height: 21.5px;
    white-space: nowrap;
  }
  .contact-list svg { width: 11px; height: 11px; margin-right: 6px; flex: none; }
</style>
</head>
<body>
  <section class="card card--front">
    <span class="tab tab--left"></span>
    <span class="tab tab--right"></span>
    <p class="brand-name">The Loom Briefing</p>
    <p class="tagline">Corporate Workwear<span class="sep">|</span>Uniform Specialist<span class="sep">|</span>Personal Stylist</p>
  </section>

  <section class="card card--back">
    <span class="tab tab--left"></span>
    <span class="tab tab--right"></span>
    <p class="brand-name">The Loom Briefing</p>
    <span class="divider"></span>
    <div class="contact">
      <p class="person-name">Belinda Harwick</p>
      <p class="person-title">Director and Stylist</p>
      <ul class="contact-list">
        <li>
          <svg viewBox="0 0 12 12" aria-hidden="true"><circle cx="6" cy="6" r="6" fill="#e4bd58"/><path d="M3.2 7.6c0-1 1.2-1.4 2.8-1.4s2.8.4 2.8 1.4v.6H3.2z M3 5.2c.6-1 1.7-1.4 3-1.4s2.4.4 3 1.4l-.9.5-.6-.8h-3l-.6.8z" fill="#fff"/></svg>
          +61 8 7142 5809
        </li>
        <li>
          <svg viewBox="0 0 12 12" aria-hidden="true"><circle cx="6" cy="6" r="6" fill="#e4bd58"/><rect x="3" y="4" width="6" height="4.2" fill="#fff"/><path d="M3 4l3 2.3L9 4" stroke="#e4bd58" stroke-width="0.8" fill="none"/></svg>
          belinda@theloombriefing.example
        </li>
        <li>
          <svg viewBox="0 0 12 12" aria-hidden="true"><circle cx="6" cy="6" r="6" fill="#e4bd58"/><g stroke="#fff" stroke-width="0.7" fill="none"><circle cx="6" cy="6" r="3.4"/><ellipse cx="6" cy="6" rx="1.4" ry="3.4"/><path d="M2.6 6h6.8"/></g></svg>
          theloombriefing.example
        </li>
      </ul>
    </div>
  </section>
</body>
</html>
```